Harborline Lending and Capital. We provide MOSTLY residential home mortgages in Florida AND commercial loans for investment properties throughout the United states.
I would love to emulate so of the lender sites that are available on the internet but I would like to have the site as popular as possible for SEO purposes. Clients can already click the link to take them to the mortgage application where they can complete that and upload documents. If you could polish that up for me that would be great. I can also provide you with great detail on loan programs that are currently being offered. WE OFFER ALL MORTGAGE LENDING PRODUCTS. I would also like to add something in reference to the rate but I don't think it's legal to actually state or promise a rate for mortgage since they vary based on loan type, client and other criteria...

On the Harborline real estate site I would like to add a link or some way for clients to be able to put in credit card information to render services ...

Please let me know what you need from me

Thank you !!

Current link to site to improve and code

https://harborlinelendingandcapital.example/

Industry/Entity Type

Residential and commmercial lending

Coding

Coded - Design and coding required

Number of Pages Required

2 page

Requirements
Must have
• Love to integrate Mortgage interest rates even if general
Nice to have
• Link to fill out mortgage application via Quorvel LPX software

```html
<!DOCTYPE html>
<html lang="en">
<head>
<meta charset="utf-8">
<title>Harborline Lending and Capital of Florida</title>
<link href="https://fonts.googleapis.com/css2?family=Cinzel:wght@500;600;700&family=Roboto:wght@400;500;700&display=swap" rel="stylesheet">
<style>
:root{
  --dark:#1b3a17;
  --deep:#16301a;
  --lime:#8bc34a;
  --lime-light:#a5d46a;
  --ink:#222;
  --muted:#555;
  --grey:#e9e9e9;
  --white:#fff;
}
*{box-sizing:border-box;margin:0;padding:0}
html,body{width:1200px;height:4839px;overflow:hidden}
body{position:relative;font-family:"Roboto",Arial,sans-serif;color:var(--ink);background:var(--white)}
.abs{position:absolute}
.btn{position:absolute;display:flex;align-items:center;justify-content:center;gap:10px;font:700 13px "Roboto",sans-serif;text-transform:uppercase;border-radius:4px;white-space:nowrap}
.btn-dark{background:var(--dark);color:#fff}
.btn-light{background:#fff;color:var(--dark)}
.arrow-dot{width:18px;height:18px;border-radius:50%;background:currentColor;position:relative;display:inline-block;flex:none}
.arrow-dot::after{content:"";position:absolute;left:6px;top:5px;border-left:7px solid var(--dark);border-top:4px solid transparent;border-bottom:4px solid transparent}
.btn-light .arrow-dot{background:var(--dark)}
.btn-light .arrow-dot::after{border-left-color:#fff}
.btn-dark .arrow-dot{background:#fff}
.btn-dark .arrow-dot::after{border-left-color:var(--dark)}

/* header */
.site-header{left:0;top:0;width:1200px;height:107px;background:#fff;z-index:5}
.brand{left:113px;top:22px;display:flex;align-items:center;gap:12px}
.brand-mark{width:56px;height:56px;border-radius:50%;background:var(--dark)}
.brand-name{font:700 10px "Roboto",sans-serif;color:var(--dark);letter-spacing:.3px;text-transform:uppercase}
.brand-sub{font:400 9px "Roboto",sans-serif;letter-spacing:3.5px;color:var(--dark);margin-top:6px;text-transform:uppercase}
.social{width:36px;height:36px;border-radius:50%;border:1.5px solid #cfcfcf;top:23px}
.social.filled{background:var(--dark);border-color:var(--dark)}
.phone-ico{left:710px;top:22px;width:40px;height:40px;border-radius:50%;background:var(--lime);display:flex;align-items:center;justify-content:center}
.phone-text{left:764px;top:24px;font:500 14px "Roboto",sans-serif;color:#222;line-height:21px}
.phone-text b{font-weight:700}
.nav{left:293px;top:83px;width:907px;height:47px;background:var(--lime);display:flex}
.nav a{font:700 14px "Roboto",sans-serif;color:#fff;text-decoration:none;height:47px;display:flex;align-items:center;padding:0 28px}
.nav a.active{background:var(--dark);width:120px;justify-content:center}

/* hero */
.hero{left:0;top:107px;width:1200px;height:556px;background:linear-gradient(90deg,#2e4a25 0%,#4a6a3a 45%,#9aa394 70%,#c9c9c3 100%)}
.hero-title{left:116px;top:115px;font:700 50px/56px "Cinzel",serif;color:#fff}
.hero-title span{color:var(--lime-light);font-weight:500}
.hero-dots{left:45px;top:240px}
.hero-dots i{display:block;width:11px;height:11px;border:1.5px solid #fff;border-radius:50%;margin-bottom:7px}
.hero-dots i.on{background:#fff}

/* about */
.about-frame{left:118px;top:762px;width:460px;height:397px;border:2px solid var(--dark);border-radius:30px 0 30px 0}
.about-photo{left:131px;top:772px;width:447px;height:387px;background:linear-gradient(135deg,#3f4e5c,#c89e7b 55%,#e8e1d6);border-radius:30px 0 30px 0}
.h2{font:700 40px "Cinzel",serif;color:var(--dark)}
.para{font:400 14px/26px "Roboto",sans-serif;color:var(--muted)}

/* products */
.products{left:0;top:1251px;width:1200px;height:862px;background:linear-gradient(180deg,#7eb83d 0%,#8cc34c 40%,#5f9a2c 75%,#3e7a1f 100%)}
.section-title{font:600 37px "Cinzel",serif;text-align:center;width:1200px;left:0}
.rule{height:4px;width:56px;left:572px}
.card{width:302px;height:261px;background:#fff;border-radius:8px 8px 40px 8px;text-align:center;padding:20px 14px 0}
.card.dark{background:var(--deep);color:#fff}
.card .ico{width:66px;height:66px;border-radius:50%;border:2px solid #555;margin:0 auto 14px;display:flex;align-items:center;justify-content:center}
.card.dark .ico{background:var(--lime);border-color:var(--lime)}
.card h3{font:700 15px/23px "Roboto",sans-serif;text-transform:uppercase;height:46px;display:flex;align-items:center;justify-content:center}
.card p{font:400 14px/22px "Roboto",sans-serif;color:#555;margin-top:6px}
.card.dark p{color:#e6e6e6}
.card .go{margin-top:8px}

/* properties */
.properties{left:0;top:2113px;width:1200px;height:539px;background:var(--grey)}
.prop{width:233px;height:304px;background:#fff;border-radius:8px;overflow:hidden;box-shadow:0 2px 6px rgba(0,0,0,.12)}
.prop .img{height:247px}
.prop h4{font:700 15px "Roboto",sans-serif;text-align:center;margin-top:20px;text-transform:uppercase}
.circle-nav{width:40px;height:40px;border-radius:50%;border:1.5px solid #333;display:flex;align-items:center;justify-content:center}
.circle-nav.solid{background:#555;border-color:#ccc;box-shadow:0 0 0 4px #d8d8d8}

/* rates */
.rates-frame{left:631px;top:2748px;width:451px;height:439px;border:2px solid var(--dark);border-radius:30px 30px 30px 0}
.rates-photo{left:614px;top:2766px;width:449px;height:436px;background:linear-gradient(160deg,#f2f2f2,#c9cdd1 45%,#e07a2a 60%,#6d5f55 85%,#2f2a27);border-radius:0 20px 20px 0}
.stats{left:103px;top:3063px;width:673px;height:199px;background:#fff;border-radius:30px;border:1px solid #eee;box-shadow:0 4px 14px rgba(0,0,0,.08)}
.stat{position:absolute;width:150px;text-align:center;top:30px}
.stat .ring{width:66px;height:66px;border-radius:50%;border:2px solid var(--dark);margin:0 auto;display:flex;align-items:center;justify-content:center;font:500 21px "Roboto",sans-serif;box-shadow:0 0 0 5px #eef3e8}
.stat p{font:500 15px/24px "Roboto",sans-serif;margin-top:14px}

/* loan programs */
.programs{left:0;top:3350px;width:1200px;height:275px;background:var(--deep)}
.program{width:302px;height:383px;border-radius:30px;overflow:hidden}
.program span{position:absolute;left:26px;bottom:28px;font:700 14px "Roboto",sans-serif;color:#fff}

/* contact */
.footer-bg{left:0;top:4274px;width:1200px;height:565px;background:var(--deep)}
.contact-photo{left:0;top:3980px;width:586px;height:439px;background:linear-gradient(120deg,#cdd3d6,#8a9aa3 40%,#6b7a4b 70%,#3d4a2e)}
.contact-frame{left:699px;top:3998px;width:383px;height:292px;border:2px solid var(--dark)}
.contact-box{left:417px;top:4008px;width:657px;height:458px;background:#fff}
.field{left:471px;width:536px;border-bottom:1.5px solid #555;font:400 14px "Roboto",sans-serif;color:#666;padding-bottom:8px}

/* footer */
.foot-mark{left:146px;top:4500px;width:210px;height:210px;border-radius:50%;background:#fff}
.foot-name{left:398px;top:4574px;font:700 18px "Cinzel",serif;color:#fff;letter-spacing:1.5px;text-transform:uppercase}
.foot-sub{left:386px;top:4608px;font:400 14px "Roboto",sans-serif;color:#d8d8d8;letter-spacing:8px;text-transform:uppercase}
.foot-nav{left:389px;top:4660px;display:flex;gap:14px;font:500 15px "Roboto",sans-serif;color:#fff;align-items:center}
.foot-nav i{font-style:normal;color:#bbb;font-size:22px}
.foot-social{top:4715px;width:42px;height:42px;border-radius:50%;border:1.5px solid #fff}
.foot-social.filled{background:var(--lime);border-color:var(--lime)}
.copy{left:578px;top:4727px;font:400 14px "Roboto",sans-serif;color:#ddd}
</style>
</head>
<body>

<header class="abs site-header">
  <div class="abs brand">
    <div class="brand-mark" aria-hidden="true"></div>
    <div>
      <div class="brand-name">Harborline Lending and Capital of Florida</div>
      <div class="brand-sub">Business and Commercial Division</div>
    </div>
  </div>
  <a class="abs social filled" style="left:523px" aria-label="Social profile one"></a>
  <a class="abs social" style="left:577px" aria-label="Social profile two"></a>
  <a class="abs social" style="left:630px" aria-label="Social profile three"></a>
  <div class="abs phone-ico"><svg width="18" height="18" viewBox="0 0 24 24"><path fill="#1b3a17" d="M6.6 10.8a15 15 0 0 0 6.6 6.6l2.2-2.2c.3-.3.7-.4 1-.2 1.1.4 2.3.6 3.6.6.6 0 1 .4 1 1V20c0 .6-.4 1-1 1A17 17 0 0 1 3 4c0-.6.4-1 1-1h3.5c.6 0 1 .4 1 1 0 1.3.2 2.5.6 3.6.1.3 0 .7-.2 1z"/></svg></div>
  <div class="abs phone-text">PHONE NO:<br><b>+1 (555) 014 2290</b></div>
  <a class="btn btn-dark" style="left:941px;top:17px;width:144px;height:47px;border-radius:2px">Contact Us <span class="arrow-dot"></span></a>
  <nav class="abs nav">
    <a class="active">HOME</a><a>ABOUT US</a><a>PROPERTIES</a><a>LOAN PROGRAMS</a><a>LENDING PRODUCTS</a>
  </nav>
</header>

<section class="abs hero" role="img" aria-label="Mortgage advisor meeting a couple in a bright office">
  <h1 class="abs hero-title">YOUR BEST RESOURCE<br>FOR <span>HASSLE-FREE, LOW<br>COST MORTGAGE</span><br>ORIGINATION</h1>
  <a class="btn" style="left:113px;top:355px;width:465px;height:49px;border:1.5px solid #fff;color:#fff;font-size:13px">Fill out mortgage application to begin lending pr <span class="arrow-dot" style="background:#fff"></span></a>
  <div class="abs hero-dots"><i></i><i class="on"></i><i></i></div>
</section>

<section>
  <div class="abs about-frame"></div>
  <div class="abs about-photo" role="img" aria-label="Happy family sitting together at home"></div>
  <h2 class="abs h2" style="left:631px;top:770px">ABOUT US</h2>
  <p class="abs para" style="left:631px;top:860px;width:452px">Harborline Lending Originates Residential Home loans in Florida and Commercial and business financing in all 50 States. We have over 25 years of experience in ALL types of real estate and commercial lending. We are strategically partnered to help you obtain ALL necessary components of residential and commercial lending. From the RIGHT lending partners to the best practice Insurance avenues and commercial and residential real estate partners</p>
  <a class="btn btn-dark" style="left:631px;top:1084px;width:135px;height:45px">Read More <span class="arrow-dot"></span></a>
</section>

<section class="abs products">
  <h2 class="abs section-title" style="top:54px;color:#fff">MORTGAGE LENDING PRODUCTS</h2>
  <div class="abs rule" style="top:114px;background:#fff"></div>
</section>
<div class="abs card" style="left:115px;top:1424px"><div class="ico"><svg width="34" height="34" viewBox="0 0 24 24" fill="none" stroke="#333" stroke-width="1.5"><path d="M3 11l9-7 9 7M5 10v10h14V10"/></svg></div><h3>Fixed-Rate<br>Mortgages</h3><p>Lorem ipsum dolor sit amet, consectetur adipiscing elit, sed do eiusmod tempor incididunt ut labore et dolorealiqua.</p><div class="go">&#10140;</div></div>
<div class="abs card" style="left:451px;top:1424px"><div class="ico"><svg width="34" height="34" viewBox="0 0 24 24" fill="none" stroke="#333" stroke-width="1.5"><path d="M3 11l9-7 9 7M5 10v10h14V10M9 15h6"/></svg></div><h3>Adjustable-Rate Mortgages<br>(ARMs)</h3><p>Lorem ipsum dolor sit amet, consectetur adipiscing elit, sed do eiusmod tempor incididunt ut labore et dolorealiqua.</p><div class="go">&#10140;</div></div>
<div class="abs card" style="left:785px;top:1424px"><div class="ico"><svg width="34" height="34" viewBox="0 0 24 24" fill="none" stroke="#333" stroke-width="1.5"><path d="M3 11l9-7 9 7M5 10v10h14V10M12 13v5"/></svg></div><h3>Interest-Only<br>Mortgages</h3><p>Lorem ipsum dolor sit amet, consectetur adipiscing elit, sed do eiusmod tempor incididunt ut labore et dolorealiqua.</p><div class="go">&#10140;</div></div>
<div class="abs card" style="left:115px;top:1724px"><div class="ico"><svg width="34" height="34" viewBox="0 0 24 24" fill="none" stroke="#333" stroke-width="1.5"><circle cx="12" cy="12" r="7"/><path d="M12 8v8M9.5 10h4a1.5 1.5 0 0 1 0 3h-3a1.5 1.5 0 0 0 0 3h4"/></svg></div><h3>FHA Loans (Federal Housing Administration)</h3><p>Lorem ipsum dolor sit amet, consectetur adipiscing elit, sed do eiusmod tempor incididunt ut labore et dolorealiqua.</p><div class="go">&#10140;</div></div>
<div class="abs card dark" style="left:451px;top:1724px"><div class="ico"><svg width="34" height="34" viewBox="0 0 24 24" fill="none" stroke="#1b3a17" stroke-width="1.6"><circle cx="12" cy="13" r="5"/><path d="M12 10.5v5M4 6l4 3M20 6l-4 3"/></svg></div><h3>VA Loans (Veterans<br>Affairs)</h3><p>Lorem ipsum dolor sit amet, consectetur adipiscing elit, sed do eiusmod tempor incididunt ut labore et dolorealiqua.</p></div>
<div class="abs card" style="left:785px;top:1724px"><div class="ico"><svg width="34" height="34" viewBox="0 0 24 24" fill="none" stroke="#333" stroke-width="1.5"><path d="M8 4h8l-2 4h-4zM6 12a6 6 0 0 1 12 0v6H6z"/><path d="M12 12v4"/></svg></div><h3>Conventional<br>Loans</h3><p>Lorem ipsum dolor sit amet, consectetur adipiscing elit, sed do eiusmod tempor incididunt ut labore et dolorealiqua.</p><div class="go">&#10140;</div></div>
<a class="btn btn-light" style="left:533px;top:2013px;width:134px;height:47px">Read More <span class="arrow-dot"></span></a>

<section class="abs properties">
  <h2 class="abs section-title" style="top:62px;color:var(--dark)">AVAILABLE PROPERTIES</h2>
  <div class="abs rule" style="top:118px;background:var(--dark)"></div>
  <div class="abs circle-nav solid" style="left:38px;top:307px"><svg width="14" height="14" viewBox="0 0 24 24"><path d="M15 5l-7 7 7 7" stroke="#fff" stroke-width="3" fill="none"/></svg></div>
  <div class="abs prop" style="left:113px;top:173px"><div class="img" role="img" aria-label="Modern white townhouse facade" style="background:linear-gradient(160deg,#cfd8e0,#f4f4f4 55%,#7d7f82)"></div><h4>12 Sunset Street</h4></div>
  <div class="abs prop" style="left:361px;top:173px"><div class="img" role="img" aria-label="Dark modern house at dusk" style="background:linear-gradient(160deg,#4a5d6c,#1f2a36 55%,#6b5a3f)"></div><h4>34 Union Avenue</h4></div>
  <div class="abs prop" style="left:608px;top:173px"><div class="img" role="img" aria-label="Contemporary home with wooden slats" style="background:linear-gradient(170deg,#8fb1d4,#d9dde0 55%,#8a6f51)"></div><h4>56 Washington Street</h4></div>
  <div class="abs prop" style="left:856px;top:173px"><div class="img" role="img" aria-label="Brick and glass building exterior" style="background:linear-gradient(160deg,#8c4a3a,#6a3a2e 55%,#4f6d8f)"></div><h4>78 Oak Boulevard</h4></div>
  <div class="abs circle-nav" style="left:1124px;top:307px"><svg width="14" height="14" viewBox="0 0 24 24"><path d="M9 5l7 7-7 7" stroke="#333" stroke-width="2.5" fill="none"/></svg></div>
</section>

<section>
  <h2 class="abs h2" style="left:111px;top:2728px;font-size:42px;line-height:48px">OUR MORTGAGE<br>INTEREST RATES</h2>
  <div class="abs" style="left:111px;top:2836px;width:56px;height:4px;background:var(--dark)"></div>
  <p class="abs para" style="left:111px;top:2868px;width:470px">Lorem ipsum dolor sit amet, consectetur adipiscing elit, sed do eius-mod tempor incididunt ut labore et dolore magna aliqua. Ut enim ad minim veniam, quis nostrud exercitation ullamco laboris nisi ut liuip ex ea commodo consequat. Duis aute irure dolor in.</p>
  <a class="btn btn-dark" style="left:113px;top:2984px;width:144px;height:45px">Learn More <span class="arrow-dot"></span></a>
  <div class="abs rates-frame"></div>
  <div class="abs rates-photo" role="img" aria-label="Small model house held above stacked coins"></div>
  <div class="abs stats">
    <div class="stat" style="left:17px"><div class="ring">52%</div><p>Fixed<br>Rate Mortgages</p></div>
    <div class="stat" style="left:184px"><div class="ring">82%</div><p>Adjustable-Rate<br>Mortgages</p></div>
    <div class="stat" style="left:353px"><div class="ring">57%</div><p>Interest-Only<br>Mortgages</p></div>
    <div class="stat" style="left:522px"><div class="ring">76%</div><p>Hybrid<br>ARMs</p></div>
  </div>
</section>

<section>
  <div class="abs programs">
    <h2 class="abs section-title" style="top:46px;color:#fff">OUR LOAN PROGRAMS</h2>
  </div>
  <div class="abs circle-nav solid" style="left:44px;top:3697px"><svg width="14" height="14" viewBox="0 0 24 24"><path d="M15 5l-7 7 7 7" stroke="#fff" stroke-width="3" fill="none"/></svg></div>
  <div class="abs program" style="left:113px;top:3508px" role="img" aria-label="Key with house keychain in a door lock"><div style="position:absolute;inset:0;background:linear-gradient(150deg,#6b4a35,#2b211c 60%,#1a1412)"></div><span>CONVENTIONAL LOAN &#8594;</span></div>
  <div class="abs program" style="left:449px;top:3508px" role="img" aria-label="Model house resting on a stack of documents"><div style="position:absolute;inset:0;background:linear-gradient(170deg,#a9b2b8,#d7cdbb 55%,#8e6b4e)"></div><span>USDA LOANS &#8594;</span></div>
  <div class="abs program" style="left:785px;top:3508px" role="img" aria-label="House model with a falling red arrow and keys"><div style="position:absolute;inset:0;background:linear-gradient(160deg,#2e3a4a,#7a2a2a 50%,#c8c0b0)"></div><span>JUMBO LOANS &#8594;</span></div>
  <div class="abs circle-nav" style="left:1127px;top:3697px"><svg width="14" height="14" viewBox="0 0 24 24"><path d="M9 5l7 7-7 7" stroke="#333" stroke-width="2.5" fill="none"/></svg></div>
</section>

<div class="abs footer-bg"></div>

<section>
  <div class="abs contact-photo" role="img" aria-label="Two colleagues smiling in a modern office"></div>
  <div class="abs contact-frame"></div>
  <form class="abs contact-box"></form>
  <h2 class="abs h2" style="left:471px;top:4050px;font-size:42px">GET IN TOUCH</h2>
  <div class="abs" style="left:471px;top:4108px;width:60px;height:4px;background:var(--dark)"></div>
  <div class="abs field" style="top:4142px">Name</div>
  <div class="abs field" style="top:4206px">Email</div>
  <div class="abs field" style="top:4270px">Phone Number</div>
  <div class="abs field" style="top:4334px">Message</div>
  <a class="btn btn-dark" style="left:471px;top:4385px;width:149px;height:45px">Submit Now <span class="arrow-dot"></span></a>
</section>

<footer>
  <div class="abs foot-mark" aria-hidden="true"></div>
  <div class="abs foot-name">Harborline Lending and Capital of Florida</div>
  <div class="abs foot-sub">Business and Commercial Division</div>
  <nav class="abs foot-nav"><span>HOME</span><i>/</i><span>ABOUT US</span><i>/</i><span>PROPERTIES</span><i>/</i><span>LOAN PROGRAMS</span><i>/</i><span>LENDING PRODUCTS</span></nav>
  <a class="abs foot-social filled" style="left:385px" aria-label="Social profile one"></a>
  <a class="abs foot-social" style="left:450px" aria-label="Social profile two"></a>
  <a class="abs foot-social" style="left:514px" aria-label="Video channel"></a>
  <div class="abs copy">© 2025. All Rights Reserved.</div>
</footer>

</body>
</html>
```